Pyschiatry Experts need Marketing Campaign

Ad(s) developed for print advertising sharing our purpose and services, highlighting our medical care providers. Must be welcoming and inviting while displaying a high level of professionalism expected from a physician's office.

Target Market(s)

Local community

Industry/Entity Type

Psychiatry (Healthcare)

Requirements
Must have
• Staff pictures, 'Medication Management Experts', 'Prompt Appointments', 'ADD/ADHD, Bipolar Disorder, Depression, Anxiety, Schizophrenia, Grief Reaction and others' 'Virtual and In-Person Visits'
Nice to have
• Address: 412 E Marlowe Pinecrest Falls Phone (555)555-7193 website: BrightLoftCare.com Hours: Mon - Thur 8am - 5pm

```html
<!DOCTYPE html>
<html lang="en">
<head>
<meta charset="utf-8">
<title>Brightloft Care – Medication Management Experts</title>
<link rel="stylesheet" href="https://fonts.googleapis.com/css2?family=Playfair+Display:wght@700;800&family=Nunito+Sans:wght@400;600;800&family=Arimo:wght@400;500;700&display=swap">
<style>
  :root {
    --page-bg: #ecebe6;
    --olive: #8a9150;
    --grass: #6d8a3c;
    --white: #ffffff;
    --lime: #a8e452;
    --lime-line: #8fd34a;
    --teal: #0e9482;
    --forest: #0b3a12;
    --name-yellow: #d9ef3c;
    --ink: #1e1e1e;
    --muted: #333333;
    --portrait: #8a929a;
  }
  * { box-sizing: border-box; margin: 0; padding: 0; }
  html, body {
    width: 1200px; height: 1200px; overflow: hidden;
    background: var(--page-bg);
  }
  .flyer {
    position: absolute; left: 203px; top: 40px;
    width: 984px; height: 1390px;
    transform: scale(0.806); transform-origin: top left;
    background: var(--white);
    overflow: hidden;
    box-shadow: 0 6px 18px rgba(0,0,0,0.25);
  }
  .hero {
    position: absolute; left: 0; top: 0; width: 984px; height: 640px;
    background: linear-gradient(180deg, var(--olive) 0%, var(--olive) 42%, #7f9448 62%, var(--grass) 100%);
  }
  .hero-photo {
    position: absolute; left: 300px; top: 330px; width: 684px; height: 300px;
    background: radial-gradient(ellipse at 60% 55%, #cfcfcf 0%, #b9b7b2 35%, rgba(120,140,80,0) 70%);
  }
  .headline {
    position: absolute; left: 94px; top: 82px;
    border-left: 3px solid var(--white);
    padding-left: 38px;
    font-family: "Playfair Display", Georgia, serif;
    font-weight: 800; font-size: 64px; line-height: 66px;
    color: var(--white);
  }
  .curves { position: absolute; left: 0; top: 0; width: 984px; height: 1390px; }
  .brand {
    position: absolute; left: 60px; top: 700px; width: 390px;
    display: flex; flex-direction: column; align-items: center; gap: 22px;
  }
  .brand-dot { width: 96px; height: 96px; border-radius: 50%; background: var(--teal); }
  .brand-name {
    font-family: "Nunito Sans", Arial, sans-serif; font-weight: 600;
    font-size: 46px; color: var(--teal); letter-spacing: 1px; white-space: nowrap;
  }
  .prompt {
    position: absolute; left: 509px; top: 685px; width: 428px; height: 60px;
    border-radius: 30px; background: var(--teal); color: var(--white);
    font-family: "Nunito Sans", Arial, sans-serif; font-weight: 800; font-size: 28px;
    display: flex; align-items: center; justify-content: center; letter-spacing: 0.5px;
  }
  .conditions {
    position: absolute; top: 760px; list-style: none;
    font-family: "Nunito Sans", Arial, sans-serif; font-size: 24px; color: var(--ink);
    line-height: 35px;
  }
  .conditions li::before { content: "• "; font-weight: 800; }
  .conditions.col-a { left: 520px; }
  .conditions.col-b { left: 745px; }
  .team {
    position: absolute; left: 48px; top: 948px; width: 888px;
    display: flex; justify-content: space-between;
  }
  .provider { position: relative; width: 195px; height: 260px; }
  .provider-card {
    position: absolute; left: 0; top: 148px; width: 195px; height: 112px;
    background: var(--forest); border-radius: 14px;
    text-align: center; padding-top: 50px;
    font-family: "Nunito Sans", Arial, sans-serif; color: var(--name-yellow);
  }
  .provider-name { font-size: 22px; font-weight: 600; line-height: 26px; }
  .provider-cred { font-size: 16px; line-height: 20px; }
  .provider-ring {
    position: absolute; left: 0; top: 0; width: 195px; height: 195px; border-radius: 50%;
    background: var(--forest); padding: 8px;
  }
  .provider-ring-inner {
    width: 100%; height: 100%; border-radius: 50%; background: var(--lime); padding: 3px;
  }
  .provider-photo {
    width: 100%; height: 100%; border-radius: 50%;
    background: radial-gradient(circle at 50% 40%, #c9b3a4 0%, #9a8c84 40%, var(--portrait) 75%);
  }
  .details {
    position: absolute; left: 48px; top: 1228px; width: 890px; display: flex;
    font-family: "Arimo", Arial, sans-serif; color: var(--ink);
  }
  .detail { padding: 0 9px; border-left: 1.5px solid var(--muted); }
  .detail:first-child { border-left: 0; padding-left: 4px; }
  .detail-label { font-size: 16px; color: var(--muted); line-height: 24px; }
  .detail-value { font-size: 20px; font-weight: 500; line-height: 32px; white-space: nowrap; }
  .visits {
    position: absolute; left: 48px; top: 1302px; width: 888px; height: 42px;
    border-radius: 21px; background: var(--forest); color: var(--white);
    font-family: "Nunito Sans", Arial, sans-serif; font-weight: 800; font-size: 24px;
    display: flex; align-items: center; justify-content: center; letter-spacing: 0.5px;
  }
</style>
</head>
<body>
  <main class="flyer">
    <div class="hero" role="img" aria-label="Photo of a smiling woman relaxing on green grass with a leaf motif">
      <div class="hero-photo"></div>
    </div>
    <h1 class="headline">Medication<br>Management<br>Experts</h1>

    <svg class="curves" viewBox="0 0 984 1390" aria-hidden="true">
      <path d="M0 568 Q480 690 984 568 L984 1390 L0 1390 Z" fill="#ffffff"/>
      <path d="M0 568 Q480 690 984 568" fill="none" stroke="#8fd34a" stroke-width="7"/>
      <path d="M0 1095 Q492 985 984 1080 L984 1390 L0 1390 Z" fill="#a8e452"/>
    </svg>

    <div class="brand">
      <div class="brand-dot"></div>
      <div class="brand-name">BRIGHTLOFT CARE</div>
    </div>

    <div class="prompt">PROMPT APPOINTMENTS</div>
    <ul class="conditions col-a">
      <li>ADD/ADHD</li>
      <li>Bipolar Disorder</li>
      <li>Depression</li>
      <li>Anxiety</li>
    </ul>
    <ul class="conditions col-b">
      <li>Schizophrenia</li>
      <li>Grief Reaction</li>
      <li>and others</li>
    </ul>

    <section class="team">
      <div class="provider">
        <div class="provider-card"><div class="provider-name">Evan Marsh</div><div class="provider-cred">PMHNP - BC</div></div>
        <div class="provider-ring"><div class="provider-ring-inner"><div class="provider-photo" role="img" aria-label="Portrait photo of provider Evan Marsh"></div></div></div>
      </div>
      <div class="provider">
        <div class="provider-card"><div class="provider-name">Dana Whitcomb</div><div class="provider-cred">PMHNP - BC</div></div>
        <div class="provider-ring"><div class="provider-ring-inner"><div class="provider-photo" role="img" aria-label="Portrait photo of provider Dana Whitcomb"></div></div></div>
      </div>
      <div class="provider">
        <div class="provider-card"><div class="provider-name">Neil Forsberg</div><div class="provider-cred">PMHNP - BC</div></div>
        <div class="provider-ring"><div class="provider-ring-inner"><div class="provider-photo" role="img" aria-label="Portrait photo of provider Neil Forsberg"></div></div></div>
      </div>
      <div class="provider">
        <div class="provider-card"><div class="provider-name">Ruth Aldane</div><div class="provider-cred">PMHNP-BC, DNP</div></div>
        <div class="provider-ring"><div class="provider-ring-inner"><div class="provider-photo" role="img" aria-label="Portrait photo of provider Ruth Aldane"></div></div></div>
      </div>
    </section>

    <section class="details">
      <div class="detail"><div class="detail-label">Hours:</div><div class="detail-value">Mon - Thur 8am - 5pm</div></div>
      <div class="detail"><div class="detail-label">Address:</div><div class="detail-value">412 E Marlowe Pinecrest Falls</div></div>
      <div class="detail"><div class="detail-label">Phone:</div><div class="detail-value">(555)555-7193</div></div>
      <div class="detail"><div class="detail-label">Website:</div><div class="detail-value">BrightLoftCare.com</div></div>
    </section>

    <div class="visits">VIRTUAL AND IN-PERSON VISITS</div>
  </main>
</body>
</html>
```